Quillbrookes websites redesign

Www.quill-brookes.com needs to be redesigned along with updations. The incremental material will be provided for the updations. We are looking for complete redesign of the pages with the new content. The complete write up will be provided soon

Target Market(s)

Global

Coding

Coded - Design and coding required

Number of Pages Required

5+ page

Requirements
Must have
• A clean and slick design for the Consulting.
Should not have
• Too many pictures which reduces the speed of the site

```html
<!DOCTYPE html>
<html lang="en">
<head>
<meta charset="utf-8">
<title>Quillbrookes Consultancy</title>
<link href="https://fonts.googleapis.com/css2?family=PT+Sans:ital,wght@0,400;0,700;1,400&display=swap" rel="stylesheet">
<style>
:root{
  --brand-red:#6b1f2a;
  --ink:#333a48;
  --muted:#6a6f78;
  --navy:#273650;
  --teal:#2f8db0;
  --teal-dark:#22708e;
  --page:#f7f7f7;
  --line:#dcdcdc;
  --white:#ffffff;
}
*{margin:0;padding:0;box-sizing:border-box}
html,body{width:967px;height:1200px;overflow:hidden}
body{position:relative;background:var(--page);font-family:'PT Sans',sans-serif;color:var(--ink)}
.abs{position:absolute}
.top-rule,.bottom-rule{left:0;width:967px;height:3px;background:var(--brand-red)}
.top-rule{top:0}.bottom-rule{bottom:0}

.brand{left:80px;top:34px;display:flex;align-items:center;gap:8px}
.brand-dot{width:30px;height:30px;border-radius:50%;background:var(--navy)}
.brand-name{font-size:27px;color:var(--navy);line-height:1}
.call{right:78px;top:20px;font-size:11.5px;color:var(--muted);display:flex;align-items:center;gap:4px}
.call b{color:var(--teal);font-weight:400;font-size:12px}
.nav{left:414px;top:55px;display:flex;gap:0;font-size:12.5px;color:var(--ink)}
.nav a{color:inherit;text-decoration:none;margin-right:29px;padding-bottom:5px}
.nav a.active{color:var(--brand-red);border-bottom:2px solid var(--brand-red)}
.search{left:875px;top:58px}

.hero{left:0;top:100px;width:967px;height:398px;background:radial-gradient(ellipse at 60% 40%,#1f68b0 0%,#144680 45%,#0c2550 100%)}
.hero-inner{left:0;top:100px;width:967px;height:398px;text-align:center;color:var(--white)}
.hero-brand{position:absolute;left:0;right:0;top:130px;display:flex;justify-content:center;align-items:center;gap:12px}
.hero-brand .brand-dot{width:42px;height:42px;background:var(--white)}
.hero-brand span{font-size:34px}
.hero-text{position:absolute;left:252px;width:465px;top:193px;font-size:11px;line-height:21px;text-align:left}
.hero-btn{position:absolute;left:416px;top:266px;width:131px;height:34px;background:linear-gradient(#3497ba,#22708e);border-radius:2px;font-size:12.5px;line-height:34px}
.chev{top:280px}

.welcome{left:0;width:967px;top:519px;display:flex;justify-content:center;align-items:center;gap:10px;font-size:20px;color:var(--ink)}
.welcome .brand-dot{width:24px;height:24px}
.welcome em{font-style:normal;color:var(--brand-red)}
.intro{left:190px;width:587px;top:554px;font-size:11px;line-height:21px;color:var(--muted);text-align:center}

.card{top:614px;width:188px;height:201px;background:var(--white);border:1px solid var(--line);box-shadow:0 1px 2px rgba(0,0,0,.06)}
.card-photo{height:134px;margin:1px}
.card h3{position:absolute;left:18px;top:148px;font-weight:400;font-size:13.5px;color:var(--ink)}
.card p{position:absolute;left:17px;top:172px;font-style:italic;font-size:11px;color:#8a8f98}
.card svg{position:absolute;right:21px;top:170px}

.band{left:0;top:853px;width:967px;height:254px;background:var(--navy);color:var(--white)}
.band h2{position:absolute;font-weight:400;font-size:17.5px}
.about-photo{left:82px;top:932px;width:173px;height:128px;background:linear-gradient(135deg,#7a3540,#b0485a 60%,#c98a3c);border:1px solid #8a8f98}
.about-text{left:278px;top:932px;width:255px;font-size:9.5px;line-height:17.5px;color:#dde2ea}
.more-btn{left:279px;top:1034px;width:91px;height:26px;border:1.5px solid #c9ced8;font-size:10.5px;line-height:23px;text-align:center;color:var(--white)}
.contact-note{left:575px;top:925px;font-size:9.5px;color:#dde2ea}
.field{background:var(--white);font-size:8.5px;color:#8a8f98;padding:6px 10px}
.submit{left:741px;top:1019px;width:85px;height:25px;background:linear-gradient(#3497ba,#22708e);border-radius:2px;font-size:11px;line-height:25px;text-align:center;color:var(--white)}

.foot-nav{left:78px;top:1130px;font-size:11px;color:var(--muted);word-spacing:3px}
.copyright{left:78px;top:1153px;font-size:10.5px;color:var(--muted)}
.follow{left:687px;top:1145px;font-size:10.5px;color:var(--muted)}
.socials{left:744px;top:1139px;display:flex;gap:6px}
.socials span{width:24px;height:24px;border:1.5px solid #7a7f88;border-radius:50%}
</style>
</head>
<body>
<div class="abs top-rule"></div>

<div class="abs brand"><span class="brand-dot"></span><span class="brand-name">Quillbrookes</span></div>
<div class="abs call">
  <svg width="10" height="10" viewBox="0 0 24 24"><path fill="#2f8db0" d="M6.6 10.8a15 15 0 0 0 6.6 6.6l2.2-2.2c.3-.3.7-.4 1-.2 1.1.4 2.3.6 3.6.6.6 0 1 .4 1 1V20c0 .6-.4 1-1 1A17 17 0 0 1 3 4c0-.6.4-1 1-1h3.5c.6 0 1 .4 1 1 0 1.3.2 2.5.6 3.6.1.3 0 .7-.2 1z"/></svg>
  <b>Call Now</b> : + 000 555 0142
</div>
<nav class="abs nav">
  <a class="active">Home</a><a>Founder</a><a>Consultancy</a><a>System</a><a>Case Studies</a><a>Contact</a>
</nav>
<svg class="abs search" width="11" height="11" viewBox="0 0 12 12"><circle cx="5" cy="5" r="3.6" fill="none" stroke="#333a48" stroke-width="1.6"/><path d="M7.6 7.6L11 11" stroke="#333a48" stroke-width="1.8"/></svg>

<div class="abs hero" role="img" aria-label="Hero photo: businessman touching a glowing blue network of connected nodes"></div>
<div class="abs hero-inner">
  <div class="hero-brand"><span class="brand-dot"></span><span>Quillbrookes</span></div>
  <p class="hero-text">Quillbrookes Consultancy Limited capitalizes on synergies arising from trade and investment linkages between countries and knowledge of traditional and non-traditional pools of liquidity to provide consultancy services to Emerging country banks, Corporates</p>
  <div class="hero-btn">View More &gt;&gt;</div>
</div>
<svg class="abs chev" style="left:23px" width="14" height="40" viewBox="0 0 14 40"><path d="M13 1L1 20l12 19" fill="none" stroke="#c9d6ea" stroke-width="1"/></svg>
<svg class="abs chev" style="left:930px" width="14" height="40" viewBox="0 0 14 40"><path d="M1 1l12 19L1 39" fill="none" stroke="#c9d6ea" stroke-width="1"/></svg>

<div class="abs welcome"><span class="brand-dot"></span><span>Welcome to <em>Quillbrookes</em></span></div>
<p class="abs intro">Quillbrookes Consultancy Limited capitalizes on synergies arising from trade and investment linkages between countries and knowledge of traditional and non-traditional pools of liquidity to provide consultancy</p>

<div class="abs card" style="left:80px">
  <div class="card-photo" role="img" aria-label="Photo: business team meeting in a bright boardroom" style="background:linear-gradient(#b9c4cf,#6f7a86)"></div>
  <h3>Export Credit Agency</h3><p>Click here for more info</p>
  <svg width="18" height="18" viewBox="0 0 18 18"><circle cx="9" cy="9" r="8" fill="none" stroke="#7a7f88" stroke-width="1.3"/><path d="M7.5 6l3 3-3 3" fill="none" stroke="#7a7f88" stroke-width="1.3"/></svg>
</div>
<div class="abs card" style="left:286px">
  <div class="card-photo" role="img" aria-label="Photo: two colleagues reviewing documents at a desk" style="background:linear-gradient(#d8dde2,#5d6066)"></div>
  <h3>Introducing Regional</h3><p>Click here for more info</p>
  <svg width="18" height="18" viewBox="0 0 18 18"><circle cx="9" cy="9" r="8" fill="none" stroke="#7a7f88" stroke-width="1.3"/><path d="M7.5 6l3 3-3 3" fill="none" stroke="#7a7f88" stroke-width="1.3"/></svg>
</div>
<div class="abs card" style="left:492px">
  <div class="card-photo" role="img" aria-label="Photo: group of business professionals standing together" style="background:linear-gradient(#e4e6e8,#4a4d55)"></div>
  <h3>Structured Financing</h3><p>Click here for more info</p>
  <svg width="18" height="18" viewBox="0 0 18 18"><circle cx="9" cy="9" r="8" fill="none" stroke="#7a7f88" stroke-width="1.3"/><path d="M7.5 6l3 3-3 3" fill="none" stroke="#7a7f88" stroke-width="1.3"/></svg>
</div>
<div class="abs card" style="left:698px">
  <div class="card-photo" role="img" aria-label="Photo: businesswoman presenting a digital globe with network icons" style="background:radial-gradient(circle at 45% 45%,#8fd0f2,#2a7fc4 60%,#1b5a9c)"></div>
  <h3>Bank Lines Business</h3><p>Click here for more info</p>
  <svg width="18" height="18" viewBox="0 0 18 18"><circle cx="9" cy="9" r="8" fill="none" stroke="#7a7f88" stroke-width="1.3"/><path d="M7.5 6l3 3-3 3" fill="none" stroke="#7a7f88" stroke-width="1.3"/></svg>
</div>

<section class="abs band">
  <h2 style="left:82px;top:34px">About quill-brookes</h2>
  <h2 style="left:574px;top:34px">Contact Details</h2>
</section>
<div class="abs about-photo" role="img" aria-label="Photo: speaker addressing a business forum behind a floral podium"></div>
<p class="abs about-text">The Consultancy provides bank neutral views to Corporates and SMEs in Asian emerging markets and helps in improving financial structure and efficient use of funds. Our endeavor is to provide a distinct bottom line advantage to our clients. The primary focus is in regionalisation of the banking</p>
<div class="abs more-btn">More Info &nbsp;»</div>
<p class="abs contact-note">Quillbrookes Consultancy Limited capitalizes on synergies arising from trade</p>
<div class="abs field" style="left:575px;top:953px;width:149px;height:23px">Name :</div>
<div class="abs field" style="left:575px;top:987px;width:149px;height:23px">Email :</div>
<div class="abs field" style="left:575px;top:1020px;width:149px;height:23px">Phone :</div>
<div class="abs field" style="left:741px;top:953px;width:147px;height:56px">Message :</div>
<div class="abs submit">Submit</div>

<p class="abs foot-nav">Home &nbsp;/ &nbsp;Founder &nbsp;/ &nbsp;Consultancy &nbsp;/ &nbsp;System &nbsp;/ &nbsp;Case Studies &nbsp;/ &nbsp;Contact</p>
<p class="abs copyright">Copyright © 2016. quill-brookes. All rights reserved.</p>
<p class="abs follow">Follow Us :</p>
<div class="abs socials"><span></span><span></span><span></span><span></span><span></span></div>

<div class="abs bottom-rule"></div>
</body>
</html>
```